Design for a real estate wev portal

Contents and features of the site
---------------------------------
Website in 5 languages: French, Dutch, English, German, Spanish.
English name of the site: Harbor Nest Place
Main purpose of the site:
- allow people to rent their house/ appartment for flatsharing purposes.
- help people wanting to find a room in flatsharing
- help people to find additional roommates for their flatsharing
Key interaction sequence:
1. I create a "group" of people who have common interest/hobbies
2. People who have the same interests/hobbies join my group
3. I look for a house/appartment to host my group
Website structure will be the following:
- Home
- Groups
-- Look for a group
--- Join a group
-- Create a group
- Properties
-- Look for a house/appartement
-- Apply
- Sales conditions
- Contact
- My account
-- My profile
-- My groups OR my properties
Your mission
------------
The client has no graphical guidelines, simply a logo (see attached).
We need a (responsive compliant) design for the following pages (we expect PSD's from you. No HTML nor CSS):
1. homepage (see example and wireframe attached)
2. properties search result list (see wireframe attached)
3. "detailed" form for properties
4. groups search result list
5. "detailed" form for groups
6. my account page
FOR THE COMPETITION step we only expect from you the design of first 2 screens.
Based on that, we will select the designer who will win the project, and will have to design the 4 remaining screens.
Target Market(s)
B2C
Industry/Entity Type
Real Estate
Number of Pages Required
5+ page
Look and feel
Each slider illustrates characteristics of the customer's brand and the style your logo design should communicate.

```html
<!DOCTYPE html>
<html lang="en">
<head>
<meta charset="utf-8">
<title>Harbor Nest Place — Flatsharing Portal</title>
<link rel="stylesheet" href="https://fonts.googleapis.com/css2?family=Mulish:wght@400;600;700&display=swap">
<style>
:root{
  --teal:#1b9db2;
  --teal-light:#3bbfcf;
  --teal-dark:#137f98;
  --green:#69b845;
  --ink:#2d2d2d;
  --text:#555;
  --muted:#9a9a9a;
  --line:#d9d9d9;
  --footer:#f1f1f1;
  --white:#fff;
}
*{box-sizing:border-box;margin:0;padding:0}
html,body{width:1200px;height:2406px;overflow:hidden;background:var(--white)}
body{position:relative;font-family:"Mulish",sans-serif;color:var(--ink)}
.abs{position:absolute}
a{color:inherit;text-decoration:none}

/* header */
.lang{left:155px;top:16px;width:93px;height:26px;border:1px solid var(--line);font-size:12px;display:flex;align-items:center;gap:6px;padding-left:8px;color:var(--ink)}
.lang .flag{width:16px;height:11px;background:#c9d3e6}
.account-links{right:145px;top:16px;display:flex;gap:18px;font-size:13px;color:var(--teal);text-transform:uppercase;letter-spacing:.3px}
.account-links span{display:flex;align-items:center;gap:5px}
.nav{top:80px;display:flex;font-size:15px;text-transform:uppercase;letter-spacing:.3px}
.nav a{padding:0 14px;border-left:1px solid var(--line);line-height:20px}
.nav a:first-child{border-left:none;padding-left:0}
.nav .active{color:var(--teal)}
.nav-left{left:155px}
.nav-right{left:717px}
.brand{left:500px;top:40px;width:200px;display:flex;align-items:center;gap:8px;font-size:22px;font-weight:700;color:var(--teal);line-height:1.1}
.brand .dot{width:14px;height:14px;border-radius:50%;background:var(--green);flex:none}

/* hero */
.hero{left:0;top:128px;width:1200px;height:413px;background:linear-gradient(180deg,#b9c6c9 0%,#9aa58c 55%,#5f8a3a 100%)}
.hero-dots{left:561px;top:497px;display:flex;gap:8px}
.hero-dots i{width:12px;height:12px;border-radius:50%;background:#fff}
.hero-dots i:first-child{background:#222}

/* intent boxes */
.intent{top:568px;width:454px;height:284px;border:1px solid var(--line)}
.intent h2{position:absolute;left:0;right:0;top:22px;text-align:center;font-size:24px;font-weight:600}
.intent.seek{left:136px}.intent.seek h2{color:var(--teal)}
.intent.own{left:608px}.intent.own h2{color:var(--green)}
.tile{position:absolute;top:71px;width:199px;height:175px}
.tile .photo{height:101px;background:linear-gradient(135deg,#d8d2c8,#8f8a80)}
.tile .label{height:74px;padding:16px 18px;color:#fff;font-size:17px;line-height:1.25}
.seek .label{background:var(--teal)}
.own .label{background:var(--green)}
.t1{left:23px}.t2{left:234px}

/* spotlight */
.spot-title{top:888px;font-size:27px;font-weight:400}
.card{width:454px;height:153px;border:1px solid var(--line)}
.card .photo{position:absolute;left:0;top:0;width:166px;height:151px;background:linear-gradient(135deg,#e7c9b0,#b58d6f)}
.card .photo.house{background:linear-gradient(180deg,#9cc4e4 0%,#b7b1a6 60%,#6d9b48 100%)}
.card .info{position:absolute;left:188px;top:18px;right:12px;font-size:13px;line-height:20px;color:var(--text)}
.card h3{font-size:14px;font-weight:600;text-transform:uppercase;color:var(--teal);margin-bottom:4px}
.card dl{display:grid;grid-template-columns:120px 1fr}
.card dt{color:var(--muted)}
.btn-more{height:32px;width:162px;display:flex;align-items:center;justify-content:space-between;padding-left:14px;color:#fff;font-size:13px}
.btn-more .arr{width:28px;height:32px;display:flex;align-items:center;justify-content:center;background:rgba(255,255,255,.18)}
.btn-more.groups{background:var(--teal)}
.btn-more.houses{background:var(--green)}

/* selling points */
.selling{left:0;top:1360px;width:1200px;height:360px;background:linear-gradient(180deg,var(--teal-light),var(--teal-dark))}
.points{top:1418px;color:#fff;width:460px}
.points h2{font-size:30px;font-weight:400;line-height:34px;margin-bottom:32px}
.points li{list-style:none;font-size:15px;line-height:31.6px;padding-left:18px;position:relative}
.points li::before{content:"";position:absolute;left:2px;top:11px;border-left:6px solid rgba(255,255,255,.7);border-top:5px solid transparent;border-bottom:5px solid transparent}

/* faq */
.faq-title{left:0;width:1200px;top:1762px;text-align:center;color:var(--green);font-size:31px;font-weight:700;line-height:40px}
.faq-item{left:178px;width:840px;display:flex;gap:11px;font-size:13.5px;line-height:21px;color:var(--text)}
.faq-item .num{flex:none;width:52px;height:52px;border-radius:50%;background:#f0f0f0;color:#999;font-size:26px;display:flex;align-items:center;justify-content:center;margin-top:-8px}
.faq-item .more{color:var(--green);font-weight:700;margin-left:8px}
.all-q{left:500px;top:2087px;width:201px;height:42px;border:2px solid var(--teal);color:var(--teal);font-size:19px;font-weight:600;display:flex;align-items:center;justify-content:center}

/* bottom bands */
.band{top:2165px;height:69px;display:flex;align-items:center;justify-content:center;color:#fff;font-size:27px}
.band.searches{left:0;width:598px;background:var(--teal)}
.band.tools{left:598px;width:602px;background:var(--green)}

/* footer */
.footer{left:0;top:2234px;width:1200px;height:172px;background:var(--footer)}
.footer-nav{left:0;width:1200px;top:2272px;display:flex;justify-content:center;gap:42px;font-size:17px;text-transform:uppercase;color:var(--ink)}
.copyright{left:0;width:1200px;top:2303px;text-align:center;font-size:12px;color:var(--text)}
.social{left:526px;top:2340px;display:flex;gap:6px}
.social i{width:32px;height:32px;border-radius:50%}
</style>
</head>
<body>

<header>
  <div class="abs lang"><span class="flag"></span>English ▾</div>
  <div class="abs account-links">
    <span><svg width="14" height="14" viewBox="0 0 14 14"><rect x="1" y="3" width="10" height="10" fill="none" stroke="currentColor" stroke-width="1.5"/><path d="M6 8l7-7" stroke="currentColor" stroke-width="1.8"/></svg>Create</span>
    <span><svg width="14" height="14" viewBox="0 0 14 14"><path d="M1 7h8M6 3l4 4-4 4" fill="none" stroke="currentColor" stroke-width="1.8"/><path d="M9 1h4v12H9" fill="none" stroke="currentColor" stroke-width="1.5"/></svg>Login</span>
    <span><svg width="14" height="14" viewBox="0 0 14 14"><circle cx="7" cy="4" r="3" fill="currentColor"/><path d="M1 14c0-4 3-6 6-6s6 2 6 6z" fill="currentColor"/></svg>My Account</span>
  </div>
  <nav class="abs nav nav-left"><a class="active">Home</a><a>About us</a><a>Services</a><a>Rent</a></nav>
  <div class="abs brand"><span class="dot"></span>Harbor Nest Place</div>
  <nav class="abs nav nav-right"><a>Testimonials</a><a>Resources</a><a>Contact</a></nav>
</header>

<section class="abs hero" role="img" aria-label="Photo of a smiling family in front of a brick house with a garden"></section>
<div class="abs hero-dots"><i></i><i></i><i></i><i></i></div>

<section class="abs intent seek">
  <h2>Searching for accommodation</h2>
  <div class="tile t1"><div class="photo" role="img" aria-label="Bright living room"></div><div class="label">I want to rent a room right now!</div></div>
  <div class="tile t2"><div class="photo" role="img" aria-label="Group of people joining hands" style="background:linear-gradient(135deg,#6b6259,#2e2a27)"></div><div class="label">I want to join a group</div></div>
</section>
<section class="abs intent own">
  <h2>I have a house for rent</h2>
  <div class="tile t1"><div class="photo" role="img" aria-label="Large house at dusk" style="background:linear-gradient(180deg,#7ea3c9,#6b5d52)"></div><div class="label">I want to advertise!</div></div>
  <div class="tile t2"><div class="photo" role="img" aria-label="Modern open-plan interior" style="background:linear-gradient(135deg,#8a6f5a,#3b3632)"></div><div class="label">Why is flatsharing Interesting for me?</div></div>
</section>

<h2 class="abs spot-title" style="left:136px">Under the Spotlight</h2>
<h2 class="abs spot-title" style="left:604px;top:891px">Under the Spotlight</h2>

<article class="abs card" style="left:136px;top:938px">
  <div class="photo" role="img" aria-label="Photo of a smiling group of people"></div>
  <div class="info"><h3>A nice group</h3>Your workers, seeking for accommo-<br>dation downtown.<br>Average age: 35 y<br>Men and women welcome</div>
</article>
<article class="abs card" style="left:136px;top:1103px">
  <div class="photo" role="img" aria-label="Photo of a group of young people"></div>
  <div class="info"><h3>Another nice group</h3>Young ladies, studying at universtity<br>seeking for accommodation close to<br>Harbor City University<br>Average age: 20 y<br>Only Women</div>
</article>
<div class="abs btn-more groups" style="left:136px;top:1272px">See more Groups<span class="arr">›</span></div>

<article class="abs card" style="left:606px;top:938px">
  <div class="photo house" role="img" aria-label="Photo of a detached house"></div>
  <div class="info"><h3>House</h3><dl><dt>Town</dt><dd>Chicago</dd><dt>Rent Per Month</dt><dd>$25</dd><dt>Availability</dt><dd>Availiable</dd></dl></div>
</article>
<article class="abs card" style="left:606px;top:1103px">
  <div class="photo house" role="img" aria-label="Photo of a white apartment building" style="background:linear-gradient(180deg,#2f7fd0,#d9e2ea)"></div>
  <div class="info"><h3>Appartment</h3><dl><dt>Town</dt><dd>Chicago</dd><dt>Rent Per Month</dt><dd>$25</dd><dt>Availability</dt><dd>Availiable</dd></dl></div>
</article>
<div class="abs btn-more houses" style="left:613px;top:1272px">See more house<span class="arr">›</span></div>

<section class="abs selling"></section>
<div class="abs points" style="left:144px">
  <h2>Key Selling Points for<br>The Roommates</h2>
  <ul><li>Morbi diam mauris viverra in gravida eu mattis in ante</li><li>Morbi eget arcu Morbi porta libero</li><li>Allamcorper nonummy nibh ligula pulvinar</li><li>Metus eget consectetuer</li><li>Augue nisi quis lacus Ut ac mi</li></ul>
</div>
<div class="abs points" style="left:651px">
  <h2>Key Selling Points for<br>The Owners</h2>
  <ul><li>Morbi diam mauris viverra in gravida eu mattis in ante</li><li>Morbi eget arcu Morbi porta libero</li><li>Allamcorper nonummy nibh ligula pulvinar</li><li>Metus eget consectetuer</li><li>Augue nisi quis lacus Ut ac mi</li></ul>
</div>

<h2 class="abs faq-title">Everything You need to Know<br>About Flatsharing</h2>
<div class="abs faq-item" style="top:1872px"><span class="num">1</span><p>Morbi diam mauris viverra in gravida eu mattis in ante Morbi eget arcu Morbi porta libero id ullamcorper nonummy nibh ligula pulvinar metus eget consectetuer augue nisi quis lacus Ut ac mi quis lacus mollis aliquam <span class="more">MORE ›</span></p></div>
<div class="abs faq-item" style="top:1942px"><span class="num">2</span><p>Curabitur iaculis tempus eros Curabitur vel mi sit amet magna malesuada ultrices Ut nisi erat fermentum vel congue id euismod in elit Fusce ultricies orci ac feugiat suscipit leo massa sodales velit et <span class="more">MORE ›</span></p></div>
<div class="abs faq-item" style="top:2012px"><span class="num">3</span><p>Curabitur tristique mi condimentum orci Phasellus pellentesque aliquam enim Proin dui lectus cursus eu mattis laoreet viverra sit amet quam Curabitur vel dolor ultrices ipsum dictum tristique Praesent vitae lacus Ut velit enim <span class="more">MORE ›</span></p></div>
<div class="abs all-q">All Questions ›</div>

<div class="abs band searches">Pre-Defined Searches</div>
<div class="abs band tools">Tools and Informations</div>

<footer class="abs footer"></footer>
<nav class="abs footer-nav"><a>Home</a><a>About us</a><a>Services</a><a>Rent</a><a>Testimonials</a><a>Resources</a><a>Contact</a></nav>
<p class="abs copyright">© 2016 Company Name &nbsp;All right reserved &nbsp;Term of Use</p>
<div class="abs social" aria-label="Social links">
  <i style="background:#3aa7e0"></i><i style="background:#3b5b9a"></i><i style="background:#1b6fa6"></i><i style="background:#d9473a"></i>
</div>

</body>
</html>
```